Website development company website

ABOUT COMPANY
Hi everyone! We're a Melbourne, Australia website development company in a need of a website design that will make online store merchants want to engage our services.
We specialise exclusively in Torvista e-commerce platform (https://torvista-platform.example/). What distinguishes our business from competition is that rather than designing and building brand new websites, we offer development, support and maintenance services to established websites. Maintenance and Support are the keywords representing our business.
Our potential clients are people with broken, slow and underperforming Torvista installations who need assistance getting their websites up and making sales. Our website must pass the message that we can help, and provide quick means of making contact.
DESIGN
Overall, we're looking for a slick, clean, airy, conservative design. No need to do anything crazy, try to stick to what's "standard" in website design these days and make it easy on all of us. The website is unlikely to be updated too often so it needs to look attractive and fresh first time over and after a year, too.
Attached is our new logo, which you'll be able to take the basic idea from, the colors and fonts. Though, don't use the fonts from the logo in the website, stick to the standard widely supported fonts. Additional use of Google fonts is fine.
Don't overdo it with colors, stick to conservative basic color set and only use the colors from the log for accents like headings etc. Please, don't be tempted to use the blue and orange as background of whole blocks, other than perhaps footer. Thanks.
For the images used, I'd like to stay away from a design studio/digital agency feel and lean more towards professional support and maintenance services. I'm thinking images of content merchants doing their job. Something along the lines of "We'll be taking care of the website so that you only need to care about the business".
Some ideas I like:
http://www.plumframe-pics.example/detail/photo/portrait-of-confident-male-design-professional-royalty-free-image/572048163
http://www.plumframe-pics.example/detail/photo/designer-taking-picture-of-hat-high-res-stock-photography/839207514
http://www.plumframe-pics.example/detail/photo/woman-packaging-pottery-royalty-free-image/216684093
Images of colorful shopping bags and shopping carts are over the top and not serious enough. Instead of images matching Online Shopping, I'd try going more for Stability, Reliability, Performance.
Our existing website is http://www.bravuln.example. Please, don't take design ideas from it, but it will give you a picture of the structure of our new website and content that's going to be used initially.
If you could include a basic icon set to use throughout the website, that would be great. If the icons could match our logo (attached), it would be a big plus.
ALL PAGES
Every page must contain clearly visible phone number (1300 648 907) and a Contact Us Now button, which opens an AJAX driven popup form with Name, Email, Phone and Message to be sent through.
To start with, main menu items will be Torvista, Portfolio, Contact.
At the bottom of each page, please, include a newsletter subscription form with text Subscribe to Torvista Support and Security Updates.
For the footer, I'd like to see a logo strip with the following logos in grayscale (no need to link anywhere): Torvista, QRX, DataVane, NCB. You'll find the logos on Google Images.
Standard footer columns follow. Here, I'd like to see logos in color: Torvista Certified Developer, Torvista Ceritified Solution Provider. Again, the logos are on Google Images.
No social media logos/links necessary anywhere on the website.
...and then the copyright line.
FRONT PAGE
Large slider with images that would appeal to our target audience. Keywords here would be Torvista System Audit, Torvista Performance Optimisation, Torvista Website Emergency Recovery, Torvista Development Infrastructure Hosting. We'll have a static page created for each of these to link to.
In a corner of the slider, or on the edge, can I have an overlay with logos in color (same as footer): Torvista Certified Developer, Torvista Ceritified Solution Provider.
Underneath, a number of blocks, each with an image and teaser that we'll use to link to various pages throughout the website.
PORTFOLIO PAGE
I'm thinking a single long page with a block per client, which will contain project name, description from us and a testimonial from client. Also, each block will contain a single large screenshot. No gallery or slideshow is necessary here, just one image per project.
I'll leave the layout up to you, but try to put yourself in the shoes of a potential client reviewing our past work by simply scrolling down this one page.
CONTACT US PAGE
Separate page with the same form as above, phone number (1300 648 907), email address (support@kavreo.example), address (Suite 42, Level 3|8 Wattlebrook Lane|Fernvale Heights VIC 3999), and a grayscale Google Map.
CODING UP
Coding up into static HTML/CSS/JS is equally important as the design itself. We're a website development company, we'll be integrating the theme. We will spot any issues and we will point them out.
Coded up design must be fully responsive. Enough said.
To be able to create any content in future, we'd like one extra page coded up with samples of all themed elements, lists, forms, buttons, 2, 3, 4-column layout, alerts, icons, etc. This page does not need to be designed, only coded up.
The design will be integrated into Drupal using Twig. If possible at all, try to keep it in mind when designing and coding up, and make the integration into a Drupal theme easier for us.
GOOD LUCK!
That's it. Let me know if anything needs clarifying. So far I've had a great experience with ArtFlockly. I don't doubt some great designs will emerge. Clever ideas are highly appreciated, but also make it clear you've read and followed the points in this brief. Cheers, Tom

```html
<!DOCTYPE html>
<html lang="en">
<head>
<meta charset="utf-8">
<title>Nexaloop Commerce — Torvista Support &amp; Maintenance</title>
<link href="https://fonts.googleapis.com/css2?family=Montserrat:ital,wght@0,400;0,500;0,600;0,700;1,400&display=swap" rel="stylesheet">
<style>
:root{
  --navy:#123f6e;
  --navy-dark:#0d2f55;
  --orange:#e8821e;
  --text:#6f6f6f;
  --heading:#222;
  --light:#f4f4f4;
  --rule:#e2e2e2;
  --footer:#1f1f1f;
  --footer-text:#cfcfcf;
}
*{box-sizing:border-box;margin:0;padding:0}
html,body{width:1200px;height:2731px;overflow:hidden}
body{position:relative;background:#fff;font-family:"Montserrat",Arial,sans-serif;color:var(--text)}
a{text-decoration:none;color:inherit}

/* header */
.site-header{position:absolute;left:0;top:0;width:1200px;height:100px;z-index:3}
.brand{position:absolute;left:112px;top:26px;display:flex;align-items:center;gap:12px}
.brand-mark{width:40px;height:46px;background:var(--orange);border-radius:4px}
.brand-name{font-weight:700;font-size:36px;color:var(--navy);letter-spacing:-0.5px;line-height:1}
.main-nav{position:absolute;top:40px;left:0;width:1200px;font-size:14px;font-weight:500;color:var(--navy-dark)}
.main-nav a{position:absolute;white-space:nowrap}
.main-nav a.is-active{color:var(--orange)}
.main-nav a.is-active::after{content:"";position:absolute;left:-8px;right:-8px;top:23px;height:2px;background:var(--orange)}

/* hero */
.hero{position:absolute;left:0;top:0;width:1200px;height:652px;overflow:hidden}
.hero-photo{position:absolute;inset:0;
  background:
    radial-gradient(ellipse 260px 200px at 120px 140px,rgba(255,255,255,.95),rgba(255,255,255,0) 70%),
    radial-gradient(ellipse 170px 120px at 930px 200px,rgba(120,130,140,.55),rgba(120,130,140,0) 70%),
    radial-gradient(ellipse 230px 190px at 200px 430px,rgba(70,90,120,.55),rgba(70,90,120,0) 70%),
    radial-gradient(ellipse 150px 130px at 510px 330px,rgba(210,170,140,.55),rgba(210,170,140,0) 70%),
    radial-gradient(ellipse 160px 140px at 780px 340px,rgba(225,195,165,.5),rgba(225,195,165,0) 70%),
    radial-gradient(ellipse 160px 140px at 1010px 420px,rgba(230,205,150,.55),rgba(230,205,150,0) 70%),
    radial-gradient(ellipse 130px 70px at 500px 560px,rgba(150,190,80,.55),rgba(150,190,80,0) 70%),
    radial-gradient(ellipse 150px 110px at 880px 520px,rgba(60,120,190,.45),rgba(60,120,190,0) 70%),
    radial-gradient(ellipse 200px 90px at 300px 520px,rgba(60,120,190,.35),rgba(60,120,190,0) 70%),
    linear-gradient(180deg,#dfe4ea 0%,#cfd6de 45%,#e4e6e8 75%,#f0f0f0 100%)}
.hero-veil{position:absolute;inset:0;background:linear-gradient(180deg,rgba(255,255,255,.8) 0%,rgba(255,255,255,.25) 30%,rgba(255,255,255,.2) 100%)}
.hero-title{position:absolute;top:318px;left:0;width:1200px;text-align:center;font-size:46px;font-weight:700;color:var(--navy);letter-spacing:.5px}
.hero-sub{position:absolute;top:382px;left:0;width:1200px;text-align:center;font-size:19px;font-weight:600;color:#222}
.btn{display:inline-block;border-radius:20px;color:#fff;font-weight:600;text-align:center}
.btn-orange{background:var(--orange)}
.btn-navy{background:var(--navy-dark)}
.hero-btn{position:absolute;left:541px;top:437px;width:160px;height:40px;line-height:40px;font-size:14px}
.hero-badges{position:absolute;left:1017px;top:556px;display:flex;gap:10px}
.badge{width:42px;height:76px;border-radius:4px}
.badge-one{background:#e07d3c}
.badge-two{background:#a9a9a9}
.slider-dots{position:absolute;left:28px;top:602px;display:flex;gap:8px}
.slider-dots span{width:28px;height:3px;background:rgba(255,255,255,.9)}
.slider-dots span.is-current{background:var(--navy)}

/* features */
.feature{position:absolute;top:700px;width:230px}
.feature-icon{height:70px;display:flex;align-items:center}
.feature h3{margin-top:28px;font-size:19px;font-weight:600;color:var(--navy)}
.feature p{margin-top:14px;font-size:11px;line-height:18px;max-height:54px;overflow:hidden;color:var(--text)}
.icon-square{width:40px;height:46px;background:var(--orange);border-radius:4px}
.platform-word{display:flex;align-items:center;gap:10px;font-size:30px;font-weight:500;color:#666}
.platform-word i{display:block;width:26px;height:26px;background:#666}
.feature-btn{position:absolute;left:111px;top:922px;width:114px;height:34px;line-height:34px;font-size:12px}
.divider{position:absolute;left:111px;top:992px;width:978px;height:1px;background:var(--rule)}

/* welcome */
.welcome-bg{position:absolute;left:0;top:993px;width:1200px;height:537px}
.welcome-title{position:absolute;left:111px;top:1140px;font-size:26px;font-weight:500;color:var(--heading)}
.welcome-text{position:absolute;left:111px;top:1200px;width:400px;font-size:11px;line-height:21px;color:var(--text)}
.welcome-btn{position:absolute;left:111px;top:1323px;width:114px;height:32px;line-height:32px;font-size:12px}
.device{position:absolute;left:524px;top:1082px;width:570px;height:360px}
.device-frame{position:absolute;left:55px;top:0;width:506px;height:330px;background:#1b1b1b;border-radius:14px}
.device-screen{position:absolute;left:14px;top:16px;width:478px;height:300px;overflow:hidden;
  background:
    radial-gradient(ellipse 70px 60px at 90px 150px,rgba(90,90,90,.45),rgba(90,90,90,0) 70%),
    radial-gradient(ellipse 60px 50px at 270px 130px,rgba(120,120,120,.4),rgba(120,120,120,0) 70%),
    radial-gradient(ellipse 60px 50px at 380px 150px,rgba(130,130,130,.4),rgba(130,130,130,0) 70%),
    linear-gradient(180deg,#f2f2f2 0%,#d6d6d6 50%,#e8e8e8 100%)}
.mini-header{position:absolute;left:0;top:0;width:100%;height:30px;background:rgba(255,255,255,.85)}
.mini-brand{position:absolute;left:12px;top:7px;display:flex;align-items:center;gap:4px;font-size:11px;font-weight:700;color:#333}
.mini-brand i{display:block;width:9px;height:11px;background:#555}
.mini-nav{position:absolute;right:12px;top:11px;display:flex;gap:12px;font-size:5px;color:#333}
.mini-title{position:absolute;left:0;top:136px;width:100%;text-align:center;font-size:16px;font-weight:700;color:#222}
.mini-sub{position:absolute;left:0;top:158px;width:100%;text-align:center;font-size:6px;font-weight:600;color:#222}
.mini-btn{position:absolute;left:219px;top:173px;width:40px;height:9px;border-radius:5px;background:#444}
.mini-badges{position:absolute;right:10px;bottom:10px;display:flex;gap:3px}
.mini-badges i{display:block;width:9px;height:16px;background:#888}
.device-base{position:absolute;left:0;top:330px;width:570px;height:14px;background:linear-gradient(180deg,#d7d7d7,#9d9d9d);border-radius:0 0 12px 12px}

/* portfolio */
.section-title{position:absolute;left:0;width:1200px;text-align:center;font-size:27px;font-weight:500;color:var(--heading)}
.portfolio-intro{position:absolute;left:245px;top:1650px;width:710px;text-align:center;font-size:10.5px;line-height:19px;color:var(--text)}
.portfolio-grid{position:absolute;left:113px;top:1726px;width:974px;height:212px;display:flex}
.tile{flex:1;position:relative;overflow:hidden}
.tile-feature{background:
    radial-gradient(ellipse 120px 90px at 170px 170px,rgba(120,170,220,.35),rgba(120,170,220,0) 70%),
    linear-gradient(135deg,#1c5088,#0e3563)}
.tile-feature h4{position:absolute;left:32px;top:30px;width:200px;font-size:19px;font-weight:400;line-height:25px;color:#fff}
.tile-feature .read-more{position:absolute;left:32px;top:158px;font-size:12px;color:#fff;display:flex;align-items:center;gap:8px}
.tile-a{background:
    radial-gradient(ellipse 80px 55px at 120px 75px,rgba(60,170,220,.9),rgba(60,170,220,0) 75%),
    radial-gradient(ellipse 60px 40px at 60px 170px,rgba(230,180,60,.7),rgba(230,180,60,0) 75%),
    radial-gradient(ellipse 70px 40px at 190px 180px,rgba(200,70,60,.55),rgba(200,70,60,0) 75%),
    linear-gradient(160deg,#5a3b22,#8a5a30 50%,#3b2a1c)}
.tile-b{background:
    radial-gradient(ellipse 90px 60px at 150px 60px,rgba(60,80,120,.9),rgba(60,80,120,0) 75%),
    radial-gradient(ellipse 60px 40px at 190px 175px,rgba(255,255,255,.95),rgba(255,255,255,0) 75%),
    radial-gradient(ellipse 70px 50px at 60px 140px,rgba(210,160,130,.7),rgba(210,160,130,0) 75%),
    linear-gradient(160deg,#2a3448,#7b8594 55%,#c8c2b6)}
.tile-c{background:
    radial-gradient(ellipse 110px 30px at 110px 95px,rgba(200,40,35,.9),rgba(200,40,35,0) 80%),
    radial-gradient(ellipse 60px 50px at 200px 180px,rgba(220,170,140,.8),rgba(220,170,140,0) 75%),
    repeating-linear-gradient(180deg,#f4f4f4 0 10px,#cfcfcf 10px 13px,#f4f4f4 13px 22px),
    #eee}
.tile-c::after{content:"";position:absolute;inset:0;background:rgba(255,255,255,.25)}

/* testimonials */
.testimonials{position:absolute;left:0;top:1996px;width:1200px;height:299px;background:var(--light)}
.testimonials .section-title{top:38px}
.quote-mark{position:absolute;font-family:Georgia,serif;font-size:90px;line-height:1;color:#d9d9d9}
.quote-text{position:absolute;left:237px;top:106px;width:700px;font-size:12px;font-style:italic;line-height:22px;color:#777}
.notch{position:absolute;left:490px;top:284px}
.clients{position:absolute;left:110px;top:2342px;width:980px;display:flex;justify-content:space-between;align-items:center}
.client{font-size:17px;font-weight:500;color:#b5b5b5}

/* footer */
.site-footer{position:absolute;left:0;top:2422px;width:1200px;height:309px;background:var(--footer);color:var(--footer-text)}
.footer-heading{position:absolute;top:36px;font-size:13px;font-weight:600;color:#fff;letter-spacing:.5px}
.contact-list{position:absolute;left:112px;top:78px;list-style:none;font-size:11px;line-height:17px}
.contact-list li{display:flex;gap:14px;margin-bottom:20px}
.contact-list svg{flex:none;margin-top:2px}
.map{position:absolute;left:361px;top:40px;width:324px;height:208px;overflow:hidden;
  background:
    radial-gradient(ellipse 90px 60px at 240px 60px,rgba(170,170,170,.6),rgba(170,170,170,0) 75%),
    radial-gradient(ellipse 100px 70px at 70px 160px,rgba(175,175,175,.6),rgba(175,175,175,0) 75%),
    linear-gradient(135deg,#dcdcdc,#c8c8c8 50%,#d4d4d4)}
.map-pin{position:absolute;left:128px;top:60px}
.partners{position:absolute;left:810px;top:100px;width:260px;display:grid;grid-template-columns:1fr 1fr;row-gap:38px;column-gap:20px}
.partner{font-size:24px;font-weight:600;color:#8c8c8c}
.copyright{position:absolute;left:0;top:284px;width:1200px;text-align:center;font-size:10px;color:#e8e8e8}
.copyright span{color:var(--orange)}
</style>
</head>
<body>

<section class="hero">
  <div class="hero-photo" role="img" aria-label="Blurred photo of a business team working at laptops in a bright office"></div>
  <div class="hero-veil"></div>
  <h1 class="hero-title">Torvista Performance Optimisation</h1>
  <p class="hero-sub">Lorem ipsum dolor sit amet, consectetur adipiscing elit.</p>
  <a class="btn btn-orange hero-btn" href="#">Learn more</a>
  <div class="slider-dots"><span class="is-current"></span><span></span><span></span></div>
  <div class="hero-badges">
    <div class="badge badge-one" role="img" aria-label="Torvista Certified Developer badge"></div>
    <div class="badge badge-two" role="img" aria-label="Torvista Ceritified Solution Provider badge"></div>
  </div>
</section>

<header class="site-header">
  <a class="brand" href="#"><span class="brand-mark"></span><span class="brand-name">Nexaloop</span></a>
  <nav class="main-nav">
    <a class="is-active" href="#" style="left:752px">Home</a>
    <a href="#" style="left:829px">About us</a>
    <a href="#" style="left:923px">Portfolio</a>
    <a href="#" style="left:1015px">Contact us</a>
  </nav>
</header>

<article class="feature" style="left:111px">
  <div class="feature-icon"><span class="icon-square"></span></div>
  <h3>Why Bravuln?</h3>
  <p>Fast Torvista-based online stores, built on time and to specification, backed by effective, focused support, means that our</p>
</article>
<article class="feature" style="left:359px">
  <div class="feature-icon"><span class="platform-word"><i></i>Torvista</span></div>
  <h3>Why Torvista?</h3>
  <p>Torvista is the world's leading open source eCommerce platform. No other open-source or free system offers out-of-the-box functionality and search</p>
</article>
<article class="feature" style="left:608px">
  <div class="feature-icon">
    <svg width="76" height="56" viewBox="0 0 76 56" aria-hidden="true">
      <g fill="#666">
        <circle cx="18" cy="13" r="8"/><circle cx="58" cy="13" r="8"/><circle cx="38" cy="11" r="10"/>
        <path d="M4 44c0-10 6-18 14-18s14 8 14 18z"/><path d="M44 44c0-10 6-18 14-18s14 8 14 18z"/>
        <path d="M22 54c0-14 7-24 16-24s16 10 16 24z"/>
      </g>
    </svg>
  </div>
  <h3>What We Do.</h3>
  <p>From support, maintenance and upgrades to redesigns, migrations and full site builds, we make your online store do what</p>
</article>
<article class="feature" style="left:858px">
  <div class="feature-icon">
    <svg width="48" height="50" viewBox="0 0 48 50" aria-hidden="true">
      <circle cx="19" cy="19" r="14" fill="none" stroke="#666" stroke-width="5"/>
      <path d="M19 11a7 7 0 0 0-7 7c0 5 7 11 7 11s7-6 7-11a7 7 0 0 0-7-7z" fill="#666"/>
      <path d="M29 30l14 14" stroke="#666" stroke-width="7" stroke-linecap="round"/>
    </svg>
  </div>
  <h3>Contact Now</h3>
  <p>Lorem ipsum dolor sit amet, consectetur adipiscing elit. Quisque molestie purus a felis condimentum molestie. Etiam a ullamcorper odio.</p>
</article>
<a class="btn btn-orange feature-btn" href="#">Contact Now</a>
<div class="divider"></div>

<svg class="welcome-bg" viewBox="0 0 1200 537" preserveAspectRatio="none" aria-hidden="true">
  <polygon points="1200,20 1200,537 0,537 0,480" fill="#f2f2f2"/>
</svg>
<h2 class="welcome-title">Welcome To Our Site</h2>
<p class="welcome-text">Lorem ipsum dolor sit amet, consectetur adipiscing elit. Quisque molestie purus a felis condimentum molestie. Etiam a ullamcorper odio. Phasellus ipsum lorem, finibus semper sollicitudin ac, varius ut velit. Maecenas hendrerit ac ligula eu ultrices.</p>
<a class="btn btn-navy welcome-btn" href="#">Show more</a>
<div class="device">
  <div class="device-frame">
    <div class="device-screen">
      <div class="mini-header">
        <span class="mini-brand"><i></i>Nexaloop</span>
        <span class="mini-nav"><span>Home</span><span>About us</span><span>Portfolio</span><span>Contact us</span></span>
      </div>
      <p class="mini-title">Torvista Performance Optimisation</p>
      <p class="mini-sub">Lorem ipsum dolor sit amet, consectetur adipiscing elit.</p>
      <span class="mini-btn"></span>
      <span class="mini-badges"><i></i><i></i></span>
    </div>
  </div>
  <div class="device-base"></div>
</div>

<h2 class="section-title" style="top:1598px">Our Portfolio</h2>
<p class="portfolio-intro">Lorem ipsum dolor sit amet, consectetur adipiscing elit. Quisque molestie purus a felis condimentum molestie. Etiam a ullamcorper odio. Phasellus ipsum lorem, finibus semper sollicitudin ac, varius ut velit. Maecenas hendrerit ac ligula eu ultrices.</p>
<div class="portfolio-grid">
  <div class="tile tile-feature">
    <h4>Suspendisse nisi erat, placerat ac ligula ut, molestie</h4>
    <a class="read-more" href="#">Read More
      <svg width="14" height="14" viewBox="0 0 14 14" aria-hidden="true"><circle cx="7" cy="7" r="6" fill="none" stroke="#fff" stroke-width="1.3"/><path d="M5 4l3 3-3 3" fill="none" stroke="#fff" stroke-width="1.3"/></svg>
    </a>
  </div>
  <div class="tile tile-a" role="img" aria-label="Photo of a laptop showing an e-commerce dashboard on a wooden desk"></div>
  <div class="tile tile-b" role="img" aria-label="Photo of hands holding a payment card over a laptop beside a cup of coffee"></div>
  <div class="tile tile-c" role="img" aria-label="Word cloud of web and e-commerce terms with a hand writing"></div>
</div>

<section class="testimonials">
  <h2 class="section-title">Our Client Testimonials</h2>
  <span class="quote-mark" style="left:188px;top:100px">&ldquo;</span>
  <p class="quote-text">Lorem ipsum dolor sit amet, consectetur adipiscing elit. Integer id elit dapibus, tempor libero non, imperdiet neque. Aenean sem elit, euismod et diam eget, fringilla euismod turpis. Aliquam in mi felis. Etiam imperdiet viverra urna, mattis accumsan felis interdumty ac. Morbi felis massa, tincidunt vitae nibh non, egestas facilisis libero. Vestibulum lorem ligula, faucibus hendrerit magna a, cursus maximus est. Proin mattis ipsum non velit sodales, in luctus ligula pretium. Donec vitae consectetur elit.</p>
  <span class="quote-mark" style="left:478px;top:218px">&rdquo;</span>
  <svg class="notch" width="44" height="16" viewBox="0 0 44 16" aria-hidden="true"><polygon points="0,15 22,0 44,15" fill="#fff"/></svg>
</section>
<div class="clients">
  <span class="client">Lacewren</span>
  <span class="client">Solvane</span>
  <span class="client">Marrowby</span>
  <span class="client">Quillmere</span>
  <span class="client">Brightfold</span>
  <span class="client">Hollowmere</span>
</div>

<footer class="site-footer">
  <h4 class="footer-heading" style="left:112px">CONTACT INFO</h4>
  <ul class="contact-list">
    <li><svg width="12" height="10" viewBox="0 0 12 10" aria-hidden="true"><rect x=".5" y=".5" width="11" height="9" fill="none" stroke="#ddd"/><path d="M.5 .5l5.5 5 5.5-5" fill="none" stroke="#ddd"/></svg>support@kavreo.example</li>
    <li><svg width="12" height="12" viewBox="0 0 12 12" aria-hidden="true"><path d="M2 1l2 0 1 3-1.5 1a7 7 0 0 0 3.5 3.5L8 7l3 1v2a1 1 0 0 1-1 1A9 9 0 0 1 1 2a1 1 0 0 1 1-1z" fill="#ddd"/></svg>1300 648 907</li>
    <li><svg width="10" height="14" viewBox="0 0 10 14" aria-hidden="true"><path d="M5 0a5 5 0 0 0-5 5c0 4 5 9 5 9s5-5 5-9a5 5 0 0 0-5-5z" fill="#ddd"/><circle cx="5" cy="5" r="2" fill="#1f1f1f"/></svg><span>Suite 42, Level 3|8 Wattlebrook Lane<br>|Fernvale Heights VIC 3999</span></li>
  </ul>
  <div class="map" role="img" aria-label="Grayscale street map of the office location">
    <svg class="map-pin" width="26" height="36" viewBox="0 0 26 36" aria-hidden="true"><path d="M13 0a13 13 0 0 0-13 13c0 10 13 23 13 23s13-13 13-23a13 13 0 0 0-13-13z" fill="#e8821e"/><circle cx="13" cy="13" r="5" fill="#fff"/></svg>
  </div>
  <h4 class="footer-heading" style="left:810px">OUR PARTNERS</h4>
  <div class="partners">
    <span class="partner">NCB</span>
    <span class="partner">QRX</span>
    <span class="partner">Torvista</span>
    <span class="partner">DataVane</span>
  </div>
  <p class="copyright">Copyright © 2016 - <span>yoursite</span></p>
</footer>

</body>
</html>
```